Email Template Design for Norvane Industrial Automation

We are looking for a skilled designer to create an engaging and visually appealing email template for Norvane Industrial Automation. The email template should be compatible with all major email clients to ensure consistent rendering across various platforms. An example email has been attached for reference, but we're open to creative interpretations that align with the brand's identity.

Deliverables:

HTML/CSS Email Template: A fully functional email template compatible with major email clients, tested for responsiveness and rendering consistency.
Images/Graphics: Any images or graphics used in the template design should be provided separately in a suitable format.

Evaluation Criteria:

Creativity and Design Aesthetics
Compatibility and Responsiveness
Alignment with Brand Identity
Clarity of Information Hierarchy
User Experience and Visual Appeal

We look forward to receiving your innovative design ideas that effectively engage and resonate with engineers in the industrial automation sector. Your contribution will play a crucial role in enhancing our email marketing efforts and promoting Norvane Industrial Automation's offerings.

Target Market(s)

Engineers in the field of industrial automation are the primary audience for this email campaign. The design should resonate with professionals who are seeking innovative solutions and products in the industrial automation sector.

Industry/Entity Type

Industrial automation

Coding

Coded - Design and coding required

Font styles to use
Sans Serif

Requirements
Must have
• 1. HTML and CSS Compatibility: The email template should be built using HTML and CSS to ensure proper rendering in different email clients. 2. Responsive Design: The template should adapt to different screen sizes, including desktop and mobile devices, to provide an optimal viewing experience. 3. Brand Consistency: The design should align with Norvane Industrial Automation's brand colors, typography, and overall visual identity. 4. Clear Call-to-Action: Include a prominent and compelling call-to-action (CTA) that drives recipients to take the desired action, such as visiting the website or exploring the featured products.
Nice to have
• - Visual Elements: Incorporate relevant images or graphics that complement the content and resonate with the industrial automation industry. - Minimalist Approach: A clean and modern design that highlights key information without overwhelming the recipient. - Dynamic Content Sections: Consider a layout that allows for customizable content sections to accommodate different campaign messages. - Brand Elements: Experiment with the integration of Norvane Industrial Automation's logo or other brand-specific elements.
Should not have
• Avoid using text as images, as this can hinder accessibility and readability. The text should be selectable and searchable within the email.

```html
<!DOCTYPE html>
<html lang="de">
<head>
<meta charset="utf-8">
<title>Norvane Industrial Automation – Newsletter</title>
<link href="https://fonts.googleapis.com/css2?family=Poppins:wght@400;500;600&family=Inter:wght@400;500&display=swap" rel="stylesheet">
<style>
  :root {
    --bg: #0c1419;
    --orange: #f7941d;
    --white: #ffffff;
    --line: #9aa3a8;
    --brand-grey: #8e969b;
    --hero-deep: #06152c;
    --hero-mid: #0e3b78;
    --hero-glow: #3a8fe0;
    --globe-dark: #03070d;
    --globe-glow: #4f8aa3;
    --module-a: #a9bff0;
    --module-b: #5f7fcf;
  }
  * { margin: 0; padding: 0; box-sizing: border-box; }
  html, body { width: 1200px; height: 2172px; overflow: hidden; background: var(--bg); }
  body { position: relative; font-family: "Poppins", sans-serif; color: var(--white); }

  .brand-name { font-family: "Poppins", sans-serif; font-weight: 500; color: var(--brand-grey); letter-spacing: 2px; }

  .site-header { position: absolute; left: 0; top: 0; width: 1200px; height: 114px; }
  .site-header .brand-name { position: absolute; left: 60px; top: 14px; font-size: 50px; line-height: 60px; }
  .main-nav { position: absolute; top: 30px; left: 0; width: 1200px; height: 40px; }
  .main-nav a { position: absolute; top: 0; color: var(--white); text-decoration: none; font-size: 22px; font-weight: 500; line-height: 32px; white-space: nowrap; }
  .main-nav a.active { color: var(--orange); border-bottom: 2px solid var(--orange); }
  .nav-cta { position: absolute; left: 945px; top: 24px; width: 195px; height: 51px; background: var(--orange); color: var(--white);
    font-size: 21px; font-weight: 500; display: flex; align-items: center; justify-content: center; text-decoration: none; }

  .hero { position: absolute; left: 0; top: 114px; width: 1200px; height: 534px; border-radius: 48px;
    background:
      radial-gradient(ellipse 22% 30% at 55% 68%, rgba(255,214,160,.55) 0%, rgba(255,214,160,0) 100%),
      radial-gradient(ellipse 60% 70% at 52% 45%, var(--hero-glow) 0%, var(--hero-mid) 50%, var(--hero-deep) 100%);
    border-bottom: 7px solid var(--orange); }

  .feature { position: absolute; left: 60px; top: 728px; width: 560px; }
  .feature-title { font-size: 25px; font-weight: 600; line-height: 42px; }
  .feature-text { margin-top: 14px; font-family: "Inter", sans-serif; font-size: 15px; line-height: 33px; width: 540px; letter-spacing: -0.1px; }
  .feature-cta { display: inline-flex; align-items: center; justify-content: center; margin-top: 22px; width: 284px; height: 51px;
    background: var(--orange); color: var(--white); font-size: 20px; font-weight: 500; text-decoration: none; }

  .feature-frame { position: absolute; left: 655px; top: 735px; width: 470px; height: 552px; border: 3px solid var(--orange); border-radius: 32px; }
  .feature-visual { position: absolute; left: 670px; top: 726px; width: 470px; height: 543px; border-radius: 30px;
    background: radial-gradient(circle at 50% 52%, var(--globe-glow) 0%, #1c3f52 30%, var(--globe-dark) 70%); }

  .products { position: absolute; left: 0; top: 1380px; width: 1200px; }
  .product { position: absolute; width: 300px; text-align: center; }
  .product-photo { width: 216px; height: 216px; border-radius: 50%; margin: 0 auto;
    background: radial-gradient(circle at 50% 50%, var(--module-b) 0%, var(--module-a) 38%, var(--white) 62%); }
  .product-name { margin-top: 22px; font-size: 20px; font-weight: 500; line-height: 30px; white-space: nowrap; }
  .product-text { margin-top: 6px; font-size: 11px; line-height: 27px; font-weight: 500; padding: 0 28px; }

  .site-footer .brand-name { position: absolute; left: 0; width: 1200px; text-align: center; top: 1868px; font-size: 50px; line-height: 60px; }
  .contact-bar { position: absolute; left: 58px; top: 1989px; width: 1018px; height: 82px; border: 2px solid var(--line); display: flex; }
  .contact-item { flex: 1; display: flex; align-items: center; justify-content: center; gap: 14px; font-family: "Inter", sans-serif; font-size: 17px; }
  .contact-item + .contact-item { border-left: 2px solid var(--line); }
  .contact-icon { width: 36px; height: 36px; border-radius: 50%; background: var(--orange); display: flex; align-items: center; justify-content: center; }
  .copyright { position: absolute; left: 0; top: 2112px; width: 1200px; text-align: center; font-family: "Inter", sans-serif; font-size: 16px; }
</style>
</head>
<body>

<header class="site-header">
  <div class="brand-name">norvane</div>
  <nav class="main-nav">
    <a class="active" href="#" style="left:484px">Home</a>
    <a href="#" style="left:571px">Kontakt</a>
    <a href="#" style="left:699px">Online</a>
    <a href="#" style="left:835px">Shop</a>
  </nav>
  <a class="nav-cta" href="#">Direkt zum Shop</a>
</header>

<section class="hero" role="img" aria-label="Hand hält ein leuchtendes Sicherheitsschloss vor einem Netzwerk aus IoT-Modulen"></section>

<section class="feature">
  <h1 class="feature-title">Norvane erweitert das Portfolio mit<br>Veltrix DAQ IoT-Komponenten<br>norvane hat das Geschäftsgebiet</h1>
  <p class="feature-text">norvane hat das Geschäftsgebiet Europa des Herstellers Kestrion und seiner Marke Veltrix DAQ übernommen, um schnell verfügbare IoT-Komponenten anzubieten. Norvane erweitert damit sein Portfolio um wichtige Netzwerktechnik-Komponenten wie spezialisierte Relais, Datenkonverter und Sensoren, die in industriellen IoT-Architekturen und Smart-Home-Anwendungen eingesetzt werden. Die Komponenten entsprechen hohen industriellen Anforderungen und Norvane unterstützt Kunden mit projektspezifischer Software-Entwicklung. Ziel ist es, kurze Lieferzeiten und schnelle Verfügbarkeit zu gewährleisten, auch bei kundenspezifischen Konfigurationen und großen Rollouts.</p>
  <a class="feature-cta" href="#">Alle Artikel von Kestrion</a>
</section>
<div class="feature-frame"></div>
<div class="feature-visual" role="img" aria-label="Hand unter einer leuchtenden vernetzten Weltkugel"></div>

<section class="products">
  <article class="product" style="left:16px">
    <div class="product-photo" role="img" aria-label="Blaues Hutschienenmodul RS232 zu RS485"></div>
    <h2 class="product-name">RS232 zu RS485</h2>
    <p class="product-text">VX2520 ist ein industrieller RS232 zu RS485-Konverter mit einem erweiterten Temperaturbereich von -25 °C bis 75 °C und einer Isolation von 3000VDC auf RS232</p>
  </article>
  <article class="product" style="left:307px">
    <div class="product-photo" role="img" aria-label="Blaues RS485-Repeatermodul"></div>
    <h2 class="product-name">RS485 repeater, isolated</h2>
    <p class="product-text">VX2510 RS485 Repeater kann die Reichweite eines RS485-Netzwerks auf bis zu 1200m erweitern. Das Modul kann auch als Signalverstärker für RS485 eingesetzt werden</p>
  </article>
  <article class="product" style="left:604px">
    <div class="product-photo" role="img" aria-label="Blaues USB-Konvertermodul"></div>
    <h2 class="product-name">USB zu RS485 I RS422 I RS232</h2>
    <p class="product-text">VX2530 USB zu RS485 ist ein industrieller Konverter für serielle Geräte über USB. Unterstützt Handshake an der RS232-Schnittstelle</p>
  </article>
  <article class="product" style="left:890px">
    <div class="product-photo" role="img" aria-label="Blaues Ethernet-Konvertermodul"></div>
    <h2 class="product-name">Ethernet zu RS485</h2>
    <p class="product-text">VX2133-485 RS485 zu Ethernet Konverter. Seriellen Geräte einfach in ein LAN-Netzwerk integrieren.</p>
  </article>
</section>

<footer class="site-footer">
  <div class="brand-name">norvane</div>
  <div class="contact-bar">
    <div class="contact-item">
      <span class="contact-icon"><svg width="18" height="18" viewBox="0 0 24 24" fill="#fff"><path d="M6.6 10.8a15 15 0 0 0 6.6 6.6l2.2-2.2c.3-.3.7-.4 1-.2 1.1.4 2.3.6 3.6.6.6 0 1 .4 1 1V20c0 .6-.4 1-1 1A17 17 0 0 1 3 4c0-.6.4-1 1-1h3.5c.6 0 1 .4 1 1 0 1.3.2 2.5.6 3.6.1.3 0 .7-.2 1z"/></svg></span>
      <span>+49(0)000 555012-0</span>
    </div>
    <div class="contact-item">
      <span class="contact-icon"><svg width="18" height="14" viewBox="0 0 24 18"><rect x="1" y="1" width="22" height="16" rx="2" fill="#fff"/><path d="M2 3l10 7 10-7" fill="none" stroke="#f7941d" stroke-width="2"/></svg></span>
      <span>info@norvane.example</span>
    </div>
    <div class="contact-item">
      <span class="contact-icon"><svg width="16" height="18" viewBox="0 0 24 24" fill="#fff"><path d="M12 2a7 7 0 0 0-7 7c0 5 7 13 7 13s7-8 7-13a7 7 0 0 0-7-7zm0 9.5A2.5 2.5 0 1 1 12 6.5a2.5 2.5 0 0 1 0 5z"/></svg></span>
      <span>Norvane, Musterstadt</span>
    </div>
  </div>
  <p class="copyright">Copyrights@2023.norvane.All Rights Reserved</p>
</footer>

</body>
</html>
```